Business card design for Virtual Assistance company

I need a business card designed for my virtual assistance company. We are a small company who services primarily C-level executive clients. The card needs to be double sided with the following contact information on the back:
Melissa Thornbury
Owner/CEO
info@rkpadvisory.net
www.rkpadvisory.net
555.302.9817

The front side should just have the company name incorporated: "RKP Advisory" and "virtual assistance"

The card should be simplistic, but eye catching and should speak to high level executives. Our primary focus areas consist of executive assistance and government contracting.

Target Market(s)

CEOs and executives

Contact Information for Business Card

see project description. phone, email, website.

Colors

Designer to choose only greyscale colors for use in the design.

```html
<!DOCTYPE html>
<html lang="en">
<head>
<meta charset="utf-8">
<title>RKP Advisory – Business Card</title>
<link rel="stylesheet" href="https://fonts.googleapis.com/css2?family=Libre+Caslon+Display&family=Libre+Caslon+Text:wght@400;700&family=Montserrat:wght@400&display=swap">
<style>
  :root {
    --backdrop: #cfd3d3;
    --paper: #ffffff;
    --ink: #111111;
    --ink-soft: #3a3a3a;
    --card-black: #0c0c0c;
    --pattern-light: #2a2a2a;
    --pattern-dark: #080808;
    --reverse-ink: #ffffff;
  }
  * { margin: 0; padding: 0; box-sizing: border-box; }
  html, body {
    width: 1200px;
    height: 1050px;
    overflow: hidden;
    background: var(--backdrop);
  }
  .sheet {
    position: relative;
    width: 1200px;
    height: 1050px;
  }
  .card {
    position: absolute;
    left: 240px;
    width: 720px;
    height: 411px;
    box-shadow: 0 18px 40px rgba(0,0,0,0.18);
  }

  /* Front (white) side */
  .card--front {
    top: 84px;
    background: var(--paper);
    color: var(--ink);
  }
  .brand-name {
    position: absolute;
    top: 78px;
    left: 0;
    width: 100%;
    text-align: center;
    font-family: "Libre Caslon Display", serif;
    font-size: 74px;
    font-weight: 400;
    letter-spacing: 0.5px;
    line-height: 1;
  }
  .brand-tagline {
    position: absolute;
    top: 168px;
    left: 0;
    width: 100%;
    padding-left: 120px;
    text-align: center;
    font-family: "Libre Caslon Text", serif;
    font-size: 25px;
    letter-spacing: 0.5px;
    text-transform: uppercase;
  }
  .holder {
    position: absolute;
    top: 228px;
    right: 408px;
    text-align: right;
  }
  .holder__name {
    font-family: "Libre Caslon Text", serif;
    font-weight: 700;
    font-size: 23px;
    line-height: 1.2;
  }
  .holder__title {
    font-family: "Montserrat", sans-serif;
    font-size: 16px;
    color: var(--ink-soft);
    margin-top: 2px;
  }
  .divider {
    position: absolute;
    top: 252px;
    left: 328px;
    width: 1px;
    height: 76px;
    background: var(--ink);
  }
  .contact-list {
    position: absolute;
    top: 244px;
    left: 346px;
    list-style: none;
    font-family: "Montserrat", sans-serif;
    font-size: 16px;
    color: var(--ink-soft);
  }
  .contact-list li {
    display: flex;
    align-items: center;
    gap: 10px;
    height: 28px;
  }
  .contact-list svg {
    width: 14px;
    height: 14px;
    fill: var(--ink);
    flex: none;
  }

  /* Back (black) side */
  .card--back {
    top: 555px;
    background: var(--card-black);
    overflow: hidden;
  }
  .monogram-field {
    position: absolute;
    inset: 0;
    background: linear-gradient(125deg, var(--pattern-light) 0%, #151515 45%, var(--pattern-dark) 100%);
  }
  .back-name {
    position: absolute;
    right: 64px;
    bottom: 62px;
    font-family: "Libre Caslon Text", serif;
    font-size: 30px;
    font-weight: 400;
    color: var(--reverse-ink);
  }
</style>
</head>
<body>
<main class="sheet">

  <section class="card card--front" aria-label="Business card front">
    <h1 class="brand-name">RKP Advisory</h1>
    <p class="brand-tagline">Virtual Assistance</p>

    <div class="holder">
      <p class="holder__name">Melissa Thornbury</p>
      <p class="holder__title">Owner/CEO</p>
    </div>

    <span class="divider"></span>

    <ul class="contact-list">
      <li>
        <svg viewBox="0 0 24 24" aria-hidden="true"><path d="M6.6 10.8a15.1 15.1 0 0 0 6.6 6.6l2.2-2.2a1 1 0 0 1 1-.25 11.4 11.4 0 0 0 3.6.57 1 1 0 0 1 1 1V20a1 1 0 0 1-1 1A17 17 0 0 1 3 4a1 1 0 0 1 1-1h3.5a1 1 0 0 1 1 1c0 1.25.2 2.45.57 3.57a1 1 0 0 1-.25 1z"/></svg>
        <span>555.302.9817</span>
      </li>
      <li>
        <svg viewBox="0 0 24 24" aria-hidden="true"><path d="M2 5h20v14H2z M2 5l10 8 10-8" fill="var(--ink)"/><path d="M2.5 5.5 12 13l9.5-7.5" stroke="#fff" stroke-width="1.6" fill="none"/></svg>
        <span>info@rkpadvisory.net</span>
      </li>
      <li>
        <svg viewBox="0 0 24 24" aria-hidden="true"><circle cx="12" cy="12" r="10"/><path d="M2 12h20M12 2c3 3 3 17 0 20M12 2c-3 3-3 17 0 20" stroke="#fff" stroke-width="1.4" fill="none"/></svg>
        <span>www.rkpadvisory.net</span>
      </li>
    </ul>
  </section>

  <section class="card card--back" aria-label="Business card back">
    <div class="monogram-field" role="img" aria-label="Tonal repeating monogram pattern in glossy black on matte black"></div>
    <p class="back-name">RKP Advisory</p>
  </section>

</main>
</body>
</html>
```